Card Design for my dog training business Brightpaw Obedience

Need a business card design for my dog training business with my new logo. Want the card to come off professional yet fun. Want it to be very eye catchy as well. I normally have these at vet clinics, pet stores, and groomers. so need it to look better than my competitors.
Target Market(s)
dog owners
Industry/Entity Type
Dog Training
Contact Information for Business Card
needs logo, my name and info
Font styles to use
Serif
Colors
0255a3
ffffff
ec1f27
000000
333333
fbfbfb
Requirements
Must have
- Brightpaw Obedience
- Felix Orland
- 415 903 2276
- info@brightpawobedience.example
- www.brightpawobedience.example

```html
<!DOCTYPE html>
<html lang="en">
<head>
<meta charset="utf-8">
<title>Brightpaw Obedience — Business Card</title>
<link href="https://fonts.googleapis.com/css2?family=Cinzel:wght@500&family=EB+Garamond:ital@1&family=Roboto:wght@300&display=swap" rel="stylesheet">
<style>
  :root {
    --backdrop: #e4e4e4;
    --card-light: #ffffff;
    --card-dark: #111111;
    --ink: #000000;
    --ink-soft: #333333;
    --mark-faint: #5a5a5a;
  }
  * { margin: 0; padding: 0; box-sizing: border-box; }
  html, body {
    width: 1125px;
    height: 1200px;
    overflow: hidden;
    background: var(--backdrop);
  }
  .card {
    position: absolute;
    left: 151px;
    width: 824px;
    height: 471px;
  }
  .card--front { top: 98px; background: var(--card-light); }
  .card--back {
    top: 631px;
    background: linear-gradient(135deg, #1c1c1c 0%, var(--card-dark) 60%, #0a0a0a 100%);
  }

  .brand {
    position: absolute;
    left: 52px;
    top: 186px;
    display: flex;
    align-items: center;
    gap: 18px;
  }
  .brand__dot {
    width: 22px;
    height: 22px;
    border-radius: 50%;
    background: var(--ink);
    flex: none;
  }
  .brand__name {
    font-family: "Cinzel", serif;
    font-weight: 500;
    font-size: 42px;
    line-height: 1.15;
    color: var(--ink);
  }

  .contact {
    position: absolute;
    right: 52px;
    top: 252px;
    text-align: right;
  }
  .contact__name {
    font-family: "Cinzel", serif;
    font-weight: 500;
    font-size: 28px;
    letter-spacing: 0.5px;
    color: var(--ink);
    margin-bottom: 16px;
  }
  .contact__list { list-style: none; }
  .contact__item {
    display: flex;
    justify-content: flex-end;
    align-items: center;
    gap: 10px;
    font-family: "Roboto", sans-serif;
    font-weight: 300;
    font-size: 18px;
    line-height: 26px;
    color: var(--ink-soft);
  }
  .contact__icon { width: 17px; height: 17px; flex: none; }
  .tagline {
    position: absolute;
    right: 52px;
    top: 402px;
    font-family: "EB Garamond", serif;
    font-style: italic;
    font-size: 20px;
    color: var(--ink);
    white-space: nowrap;
  }

  .back-mark {
    position: absolute;
    right: 56px;
    bottom: 58px;
    font-family: "Cinzel", serif;
    font-weight: 500;
    font-size: 15px;
    line-height: 1.2;
    color: var(--mark-faint);
    text-align: left;
  }
</style>
</head>
<body>
  <section class="card card--front">
    <div class="brand">
      <span class="brand__dot"></span>
      <span class="brand__name">Brightpaw<br>Obedience</span>
    </div>

    <div class="contact">
      <h1 class="contact__name">FELIX ORLAND</h1>
      <ul class="contact__list">
        <li class="contact__item">415 903 2276
          <svg class="contact__icon" viewBox="0 0 24 24" aria-hidden="true"><path fill="#333" d="M6.6 10.8a15.1 15.1 0 0 0 6.6 6.6l2.2-2.2a1 1 0 0 1 1-.25 11.4 11.4 0 0 0 3.6.57 1 1 0 0 1 1 1V20a1 1 0 0 1-1 1A17 17 0 0 1 3 4a1 1 0 0 1 1-1h3.5a1 1 0 0 1 1 1c0 1.25.2 2.45.57 3.6a1 1 0 0 1-.25 1z"/></svg>
        </li>
        <li class="contact__item">info@brightpawobedience.example
          <svg class="contact__icon" viewBox="0 0 24 24" aria-hidden="true"><path fill="#333" d="M2 5h20v14H2z M3.5 6.5 12 13l8.5-6.5" stroke="#fff" stroke-width="1.4"/></svg>
        </li>
        <li class="contact__item">www.brightpawobedience.example
          <svg class="contact__icon" viewBox="0 0 24 24" aria-hidden="true"><circle cx="12" cy="12" r="10" fill="#333"/><path d="M2 12h20M12 2c3 3 3 17 0 20M12 2c-3 3-3 17 0 20" stroke="#fff" stroke-width="1.2" fill="none"/></svg>
        </li>
      </ul>
    </div>

    <p class="tagline">“Positive training for happy dogs and proud owners.”</p>
  </section>

  <section class="card card--back">
    <div class="back-mark">Brightpaw<br>Obedience</div>
  </section>
</body>
</html>
```